Visitenkarten-Design Neutrale Verzollungs Agentur für den Grenzverkehr des Zollwesens
Sehr schnelle Umsetzung nach unserer Vorstellung,und sehr netter und guter Umgang in der Kominikation. lorvix hat unsere erwartung zu 100 % übertroffen.
Zielgruppe
Wir sind eine Neutrale Verzollungs Agentur für den Grenzverkehr des Zollwesens
Velmora & Quist Partners
Wir führen für Kunden die Zollabwicklungen ab.
Seefracht - Bahnfracht-Luftfracht-LKW Fracht
Cargo - Hersteller Firmen und Endknden International
Aufgabenstellung
Rückseite sollte mitgestaltet werden

```html
<!DOCTYPE html>
<html lang="en">
<head>
<meta charset="utf-8">
<title>Tarivo Port – Business Card</title>
<link rel="stylesheet" href="https://fonts.googleapis.com/css2?family=Open+Sans:wght@400;600;700&display=swap">
<style>
  :root {
    --stage: #1e1e1f;
    --card: #ffffff;
    --ink: #4a4a4c;
    --ink-soft: #6b6b6e;
    --blue: #4a86d0;
  }
  * { margin: 0; padding: 0; box-sizing: border-box; }
  html, body {
    width: 1200px; height: 801px; overflow: hidden;
    background: var(--stage);
    font-family: "Open Sans", Arial, sans-serif;
  }
  .stage {
    position: relative; width: 1200px; height: 801px;
    display: flex; align-items: center; justify-content: center; gap: 60px;
  }
  .card {
    position: relative; width: 520px; height: 310px;
    background: var(--card); border-radius: 4px; overflow: hidden;
    box-shadow: 0 18px 40px rgba(0,0,0,.45);
  }

  /* Front: contact side */
  .card-front .wordmark {
    position: absolute; top: 30px; right: 34px;
    font-size: 26px; font-weight: 600; color: var(--ink);
    display: flex; align-items: center; gap: 10px;
  }
  .wordmark .dot {
    width: 12px; height: 12px; border-radius: 50%; background: var(--blue);
  }
  .card-front .holder-name {
    position: absolute; right: 38px; top: 196px;
    font-size: 21px; font-weight: 400; color: var(--blue); letter-spacing: .3px;
  }
  .card-front .details {
    position: absolute; left: 150px; top: 120px;
    font-size: 12.5px; color: var(--ink-soft); line-height: 1.45;
  }
  .details .address { margin-bottom: 14px; }
  .details .contact-list { list-style: none; }
  .details .contact-list li { display: flex; align-items: center; gap: 8px; }
  .details .contact-list svg { width: 12px; height: 12px; flex: none; }
  .card-front .edge-band {
    position: absolute; left: 0; right: 0; bottom: 0; height: 10px;
    background: var(--blue);
  }

  /* Back: brand side */
  .card-back {
    display: flex; flex-direction: column; align-items: center; justify-content: center;
  }
  .card-back .wordmark {
    font-size: 46px; font-weight: 600; color: var(--ink);
    display: flex; align-items: center; gap: 16px; margin-bottom: 22px;
  }
  .card-back .wordmark .dot { width: 18px; height: 18px; }
  .card-back .tagline {
    font-size: 19px; font-weight: 700; color: var(--ink); margin-bottom: 4px;
  }
  .card-back .countries {
    font-size: 15px; color: var(--ink-soft);
  }
  .countries .sep { color: var(--blue); margin: 0 4px; }
</style>
</head>
<body>
<main class="stage">

  <section class="card card-front" aria-label="Business card front">
    <div class="wordmark"><span class="dot"></span>Tarivo Port</div>

    <div class="details">
      <p class="address">Talackerweg 48<br>4133 Pratteln Switzerland</p>
      <ul class="contact-list">
        <li>
          <svg viewBox="0 0 12 12"><path fill="#4a86d0" d="M2.5 1h2l1 2.5-1.3 1a6 6 0 0 0 3.3 3.3l1-1.3L11 7.5v2A1.5 1.5 0 0 1 9.5 11 8.5 8.5 0 0 1 1 2.5 1.5 1.5 0 0 1 2.5 1z"/></svg>
          +49 761 5550183
        </li>
        <li>
          <svg viewBox="0 0 12 12"><path fill="#4a86d0" d="M2.5 1h2l1 2.5-1.3 1a6 6 0 0 0 3.3 3.3l1-1.3L11 7.5v2A1.5 1.5 0 0 1 9.5 11 8.5 8.5 0 0 1 1 2.5 1.5 1.5 0 0 1 2.5 1z"/></svg>
          +41 61 5550247
        </li>
        <li>
          <svg viewBox="0 0 12 12"><rect x="1" y="2.5" width="10" height="7" rx="1" fill="#4a86d0"/><path d="M1.5 3l4.5 3.5L10.5 3" fill="none" stroke="#fff" stroke-width="1"/></svg>
          info@tarivo-port
        </li>
        <li>
          <svg viewBox="0 0 12 12"><circle cx="6" cy="6" r="5" fill="#4a86d0"/><path d="M1 6h10M6 1c-2 2.5-2 7.5 0 10M6 1c2 2.5 2 7.5 0 10" fill="none" stroke="#fff" stroke-width=".7"/></svg>
          www.tarivo-port.com
        </li>
      </ul>
    </div>

    <div class="holder-name">Keller Jonas</div>

    <div class="edge-band" aria-hidden="true"></div>
  </section>

  <section class="card card-back" aria-label="Business card back">
    <div class="wordmark"><span class="dot"></span>Tarivo Port</div>
    <p class="tagline">Velmora &amp; Quist Partners</p>
    <p class="countries">Switzerland<span class="sep">|</span>Germany<span class="sep">|</span>Denmark<span class="sep">|</span>France</p>
  </section>

</main>
</body>
</html>
```